Signage Design Project - For Sale and For Rent

I am looking to revamp our For Sale and For Rent signboards.
The size of the board is
1250mm WIDTH
1800mm HEIGHT
The board is one sided, and slightly curved (will not impact the design at all)
For Rent Signs need to include the following information;
NESTor Logo
For Rent
Website
Facebook link (www.socialhub.example/nestorhomesco)
Phone number 6148 7309
For Sale signs need to include the following information
NESTor logo
For Sale
Website
Facebook link
Phone number 6148 7309
One signboard with Colin Partridge (this is the agents name)
One signboard with Peter Halvey (this is the agents name)
Full service real estate for a low $5,950 (+GST)
The more bold, punch and creative the better- we are very much an innovative and young company. I would suggest visiting our website, www.nestorhomes.example.au and our facebook page to get a feel for our company.
Updates
Existing signboard + logo files have been updated.
Have also guaranteed payment.
Real Estate

```html
<!DOCTYPE html>
<html lang="en">
<head>
<meta charset="utf-8">
<title>NESTor – For Rent signboard</title>
<link rel="stylesheet" href="https://fonts.googleapis.com/css2?family=League+Gothic&family=Montserrat:wght@700&display=swap">
<style>
  :root {
    --page-bg: #e4e4e4;
    --board-bg: #e9f0e3;
    --brand-green: #6a9a56;
    --skyline-green: #a9c49a;
    --site-green: #6b9e55;
    --ink: #111111;
    --paper: #ffffff;
  }
  html, body {
    margin: 0;
    padding: 0;
    width: 1026px;
    height: 1200px;
    overflow: hidden;
    background: var(--page-bg);
  }
  .signboard {
    position: absolute;
    left: 117px;
    top: 32px;
    width: 791px;
    height: 1135px;
    display: block;
  }
  .board-face { fill: var(--board-bg); }
  .skyline { fill: var(--skyline-green); }
  .brand-name {
    font-family: "League Gothic", "Arial Narrow", sans-serif;
    font-size: 46px;
    fill: var(--brand-green);
  }
  .rule-dark { fill: var(--ink); }
  .rule-light { fill: var(--paper); }
  .headline {
    font-family: "League Gothic", "Arial Narrow", sans-serif;
    fill: var(--ink);
  }
  .headline-for { font-size: 236px; }
  .headline-rent { font-size: 176px; }
  .website {
    font-family: "League Gothic", "Arial Narrow", sans-serif;
    font-size: 36px;
    fill: var(--site-green);
  }
  .phone {
    font-family: "League Gothic", "Arial Narrow", sans-serif;
    font-size: 76px;
    fill: var(--paper);
  }
  .social-mark { fill: var(--brand-green); }
  .social-link {
    font-family: "Montserrat", Arial, sans-serif;
    font-weight: 700;
    font-size: 12.5px;
    fill: var(--paper);
  }
</style>
</head>
<body>
  <svg class="signboard" viewBox="0 0 460 660" xmlns="http://www.w3.org/2000/svg" aria-label="NESTor For Rent signboard">
    <rect class="board-face" x="0" y="0" width="460" height="660"/>

    <rect class="skyline" x="0" y="345" width="460" height="315" role="img" aria-label="Green rooftop skyline silhouette of houses and chimneys"/>

    <text class="brand-name" x="230" y="56" text-anchor="middle">NESTor</text>

    <rect class="rule-dark" x="138" y="99" width="183" height="12"/>
    <text class="headline headline-for" x="138" y="292" textLength="183" lengthAdjust="spacingAndGlyphs">FOR</text>
    <text class="headline headline-rent" x="138" y="427" textLength="183" lengthAdjust="spacingAndGlyphs">RENT</text>
    <rect class="rule-dark" x="138" y="437" width="183" height="12"/>

    <text class="website" x="138" y="494" textLength="183" lengthAdjust="spacingAndGlyphs">NESTORHOMES.EXAMPLE.AU</text>

    <rect class="rule-light" x="138" y="512" width="183" height="12"/>
    <text class="phone" x="138" y="592" textLength="183" lengthAdjust="spacingAndGlyphs">6148-7309</text>
    <rect class="rule-light" x="138" y="600" width="183" height="12"/>

    <g class="social">
      <rect class="social-mark" x="75" y="620" width="25" height="25" rx="3"/>
      <text class="social-link" x="115" y="638" textLength="275" lengthAdjust="spacingAndGlyphs">WWW.SOCIALHUB.EXAMPLE/NESTORHOMESCO</text>
    </g>
  </svg>
</body>
</html>
```